Luxury WordPress Website for CORALBASINS

I need a professional WordPress website for Coral Basins. The site should be modern, visually appealing, and user-friendly, reflecting the brand’s luxury and premium identity. It must include a homepage, product/service pages, contact form, and be responsive on both desktop and mobile devices. The design should allow for easy updates and integration of future content, while maintaining a polished and professional look.

Target Market(s)

swimmingpool & spa

Industry/Entity Type

Swimmingpool

Coding

Coded - Design and coding required

Font styles to use
Other font styles liked:
• HaboroSoft

Requirements
Must have
• Exclusive appearance
Nice to have
• • A logo that subtly incorporates water or pool elements. • A color palette that reflects luxury, elegance, and relaxation. • Clean and modern typography that is easy to read across all media. • Iconography or design elements that convey premium quality. • A versatile design that can be adapted for social media, merchandise, and promotional materials. • Optional: A tagline that emphasizes luxury and high-end pool experiences.

```html
<!DOCTYPE html>
<html lang="en">
<head>
<meta charset="utf-8">
<title>Coral Basins — Luxury Pools</title>
<link href="https://fonts.googleapis.com/css2?family=Archivo:wght@500;600;700&family=Montserrat:wght@400;500;600&display=swap" rel="stylesheet">
<style>
:root{
  --green:#b7c94f;
  --ink:#111111;
  --dark:#141414;
  --muted:#f5f5f5;
  --white:#ffffff;
  --text:#333333;
  --logo-blue:#2b79a8;
}
*{box-sizing:border-box;margin:0;padding:0}
html,body{width:1200px;height:4549px;overflow:hidden;background:var(--white)}
body{font-family:"Montserrat",sans-serif;color:var(--text);position:relative}
.abs{position:absolute}
.head{font-family:"Archivo",sans-serif;font-weight:600;text-transform:uppercase;color:var(--ink);line-height:1.12}
.label{font-family:"Archivo",sans-serif;font-weight:500;font-size:13px;color:var(--green);text-transform:uppercase;display:flex;align-items:center;gap:18px}
.label::before{content:"";width:56px;height:1px;background:var(--green)}
.btn{position:absolute;display:flex;align-items:center;justify-content:center;font-family:"Archivo",sans-serif;font-weight:600;font-size:11px;text-transform:uppercase;letter-spacing:.2px}
.btn-green{background:var(--green);color:var(--white)}
.btn-white{background:var(--white);color:var(--ink)}
.photo{position:absolute}

/* hero */
.hero{position:absolute;left:0;top:0;width:1200px;height:729px;overflow:hidden}
.hero-photo{inset:0;background:linear-gradient(180deg,#c9d3d8 0%,#b9c4bf 25%,#6f8a6a 48%,#3fa7c0 62%,#2a9bc2 80%,#5d8a4a 100%)}
.hero-shade{position:absolute;inset:0;background:linear-gradient(90deg,rgba(0,0,0,.35),rgba(0,0,0,0) 60%)}
.logo{position:absolute;font-family:"Archivo",sans-serif;font-weight:500;display:flex;align-items:center;gap:8px}
.logo .dot{width:14px;height:14px;border-radius:50%}
.hero .logo{left:76px;top:34px;color:var(--white);font-size:20px}
.hero .logo .dot{background:var(--white)}
.nav{position:absolute;top:34px;left:500px;display:flex;gap:27px;font-family:"Archivo",sans-serif;font-weight:500;font-size:11px;color:var(--white);text-transform:uppercase;align-items:center}
.hero h1{position:absolute;left:76px;top:252px;font-size:42px;color:var(--white);font-weight:600}
.hero p{position:absolute;left:76px;top:363px;width:430px;font-size:13px;line-height:22px;color:var(--white)}

/* about */
.about-text{left:549px;top:1014px;width:510px;font-size:12.5px;line-height:22.5px}

/* services */
.services{position:absolute;left:0;top:1665px;width:1200px;height:748px;background:var(--muted)}
.card{position:absolute;top:197px;width:252px;height:346px;background:var(--white);text-align:center}
.card .photo{left:6px;top:0;width:240px;height:184px}
.card h3{position:absolute;top:220px;left:0;width:100%;font-size:18px}
.card p{position:absolute;top:275px;left:30px;width:192px;font-size:11px;line-height:20px;color:#444}

/* projects */
.projects{position:absolute;left:0;top:2413px;width:1200px;height:867px}
.projects .dark{position:absolute;left:0;top:0;width:801px;height:867px;background:var(--dark)}

/* why */
.why-box{left:630px;top:3392px;width:380px;height:399px;background:var(--green)}
.why-item{position:absolute;left:34px;display:flex;gap:28px;align-items:flex-start;color:var(--white)}
.why-item b{font-family:"Archivo",sans-serif;font-weight:500;font-size:28px;line-height:1;width:36px}
.why-item span{font-size:12px;line-height:22px;width:240px}

/* contact */
.contact{position:absolute;left:0;top:3791px;width:1200px;height:343px;background:var(--ink);text-align:center;color:var(--white)}

/* footer */
.fcol h4{font-family:"Archivo",sans-serif;font-weight:600;font-size:13px;color:var(--ink);text-transform:uppercase;margin-bottom:18px}
.fcol li{list-style:none;font-size:10.5px;line-height:26.5px;color:#444}
.social{position:absolute;top:4354px;width:46px;height:46px;background:var(--ink)}
</style>
</head>
<body>

<header class="hero">
  <div class="photo hero-photo" role="img" aria-label="Photo of a blue tiled infinity pool with steel ladder beside a lawn and a modern building"></div>
  <div class="hero-shade"></div>
  <div class="logo"><span class="dot"></span>Coral Basins</div>
  <nav class="nav">
    <svg width="12" height="11" viewBox="0 0 12 11"><path d="M6 0 0 5h2v6h3V7h2v4h3V5h2z" fill="#fff"/></svg>
    <span>About Us</span><span>Our Services</span><span>Why Choose Us</span><span>Gallery</span>
  </nav>
  <a class="btn btn-white" style="left:976px;top:14px;width:148px;height:55px">Contact Us</a>
  <h1>Experience Luxury,<br>Dive Into Perfection</h1>
  <p>Transform your outdoor space with custom-designed pools that define elegance and sophistication.</p>
  <a class="btn btn-green" style="left:76px;top:427px;width:217px;height:53px">Explore Our Collections</a>
  <a class="btn btn-white" style="left:309px;top:427px;width:233px;height:53px">Get Your Free Consultation</a>
</header>

<section class="about">
  <div class="label abs" style="left:138px;top:839px">About Us</div>
  <h2 class="head abs" style="left:138px;top:872px;font-size:30px">Crafting Premium<br>Pool Experiences</h2>
  <div class="photo" style="left:143px;top:983px;width:353px;height:466px;background:linear-gradient(180deg,#8fc4ea 0%,#b9d9ee 40%,#4d7a3c 62%,#1f86a6 80%,#14617f 100%)" role="img" aria-label="Photo of palm trees and red sun loungers reflected in a resort pool"></div>
  <p class="abs about-text">At Coral Basins, we specialize in designing and building luxury swimming pools that combine aesthetic beauty with exceptional functionality. From modern infinity pools to timeless classic designs, we create outdoor sanctuaries tailored to your lifestyle.</p>
  <div class="photo" style="left:549px;top:1137px;width:266px;height:326px;background:linear-gradient(180deg,#5c8fe0 0%,#8ab1e8 25%,#7a6a4c 45%,#3f7a3a 65%,#3ab4bf 85%,#2f8f7e 100%)" role="img" aria-label="Photo of a thatched gazebo beside a tropical pool"></div>
  <div class="photo" style="left:837px;top:1137px;width:222px;height:275px;background:linear-gradient(160deg,#9fd3e6 0%,#62b5d6 50%,#3c9cc6 100%)" role="img" aria-label="Photo of steel pool ladder rails over clear blue water"></div>
  <a class="btn btn-green" style="left:549px;top:1504px;width:159px;height:53px">Read More</a>
</section>

<section class="services">
  <div class="label abs" style="left:506px;top:101px">Our Services</div>
  <h2 class="head abs" style="left:0;width:1200px;text-align:center;top:135px;font-size:29px">Bespoke Pool Solutions For Every Vision</h2>
  <div class="card" style="left:76px">
    <div class="photo" style="background:linear-gradient(180deg,#2f6fd0,#3a9be0 70%,#d7a08b)" role="img" aria-label="Photo of a pool ladder over blue water"></div>
    <h3 class="head">Custom Pool<br>Design</h3>
    <p>Personalized designs that reflect your taste and outdoor space.</p>
  </div>
  <div class="card" style="left:342px">
    <div class="photo" style="background:linear-gradient(180deg,#6e8a4a,#cfc9bc 45%,#36b4c8)" role="img" aria-label="Photo of sun loungers on a pool deck"></div>
    <h3 class="head">Pool Construction<br>&amp; Installation</h3>
    <p>Precision engineering for flawless results.</p>
  </div>
  <div class="card" style="left:607px">
    <div class="photo" style="background:linear-gradient(180deg,#cfd6dc,#3ea4c8 60%,#1f6f9a)" role="img" aria-label="Photo of a pool vacuum cleaning the water"></div>
    <h3 class="head">Maintenance<br>&amp; Upgrades</h3>
    <p>Keep your pool pristine with expert care.</p>
  </div>
  <div class="card" style="left:873px">
    <div class="photo" style="background:linear-gradient(180deg,#e0e6ea,#6c8e58 35%,#a77257 55%,#2fa7c4)" role="img" aria-label="Photo of a curved pool with wooden deck and loungers"></div>
    <h3 class="head">Luxury<br>Accessories</h3>
    <p>Lighting, heating, and water features to elevate your experience.</p>
  </div>
  <a class="btn btn-green" style="left:503px;top:606px;width:196px;height:54px">Discover Our Services</a>
</section>

<section class="projects">
  <div class="dark"></div>
  <h2 class="head abs" style="left:106px;top:84px;font-size:29px;color:var(--white)">Our Projects</h2>
  <div class="photo" style="left:102px;top:180px;width:999px;height:561px;background:linear-gradient(180deg,#c9d0d6 0%,#9aa7ae 20%,#3d6a36 45%,#7c7a6a 58%,#33a8c7 72%,#1f8fb4 88%,#b99a80 100%)" role="img" aria-label="Photo of a curved resort pool surrounded by palm trees and a pavilion"></div>
  <svg class="abs" style="left:1143px;top:443px" width="34" height="20" viewBox="0 0 34 20"><path d="M1 10h31M23 2l9 8-9 8" fill="none" stroke="#111" stroke-width="2"/></svg>
  <svg class="abs" style="left:1143px;top:494px" width="34" height="20" viewBox="0 0 34 20"><path d="M33 10H2M11 2 2 10l9 8" fill="none" stroke="#b7c94f" stroke-width="2"/></svg>
</section>

<section class="why">
  <div class="label abs" style="left:194px;top:3455px">Why Choose Us</div>
  <h2 class="head abs" style="left:194px;top:3482px;font-size:29px">Unmatched Quality.<br>Exceptional<br>Craftsmanship</h2>
  <p class="abs" style="left:192px;top:3594px;width:385px;font-size:12.5px;line-height:22px">Ut enim ad minim veniam, quis nostrud exercitation ullamco laboris nisi ut aliquip ex ea commodo consequat. Duis aute irure dolor in reprehenderit cupidatat non proident.</p>
  <div class="abs why-box">
    <div class="why-item" style="top:82px"><b>01</b><span>Expert designers and builders with years of experience.</span></div>
    <div class="why-item" style="top:150px"><b>02</b><span>Attention to detail in every project.</span></div>
    <div class="why-item" style="top:196px"><b>03</b><span>Materials and finishes that ensure durability and elegance.</span></div>
    <div class="why-item" style="top:274px"><b>04</b><span>A seamless, stress-free pool-building experience.</span></div>
  </div>
</section>

<section class="contact">
  <div class="label abs" style="left:525px;top:73px">Contact Us</div>
  <h2 class="head abs" style="left:0;width:1200px;top:105px;font-size:29px;color:var(--white)">Start Your Luxury Pool Journey Today</h2>
  <p class="abs" style="left:270px;width:660px;top:155px;font-size:12.5px;line-height:22px;color:var(--white)">Our team is ready to bring your dream pool to life. Schedule a consultation and take the first step towards a premium pool experience.</p>
  <a class="btn btn-white" style="left:503px;top:216px;width:196px;height:54px">Book A Consultation</a>
</section>

<footer>
  <div class="logo" style="left:148px;top:4278px;color:var(--logo-blue);font-size:27px"><span class="dot" style="background:var(--logo-blue)"></span>Coral Basins</div>
  <div class="social" style="left:148px"></div>
  <div class="social" style="left:203px"></div>
  <div class="social" style="left:258px"></div>
  <div class="fcol abs" style="left:397px;top:4253px">
    <h4>Quick Link</h4>
    <ul><li>Home</li><li>About Us</li><li>Our Services</li><li>Why Choose Us</li><li>Gallery</li><li>Contact Us</li></ul>
  </div>
  <div class="fcol abs" style="left:563px;top:4253px">
    <h4>Our Services</h4>
    <ul><li>Custom Pool Design</li><li>Pool Construction &amp; Installation</li><li>Maintenance &amp; Upgrades</li><li>Luxury Accessories</li></ul>
  </div>
  <div class="fcol abs" style="left:805px;top:4253px;width:280px">
    <h4>Subscribe Newsletter</h4>
    <p style="font-size:10px;line-height:17px;color:#444;width:250px">Get our monthly newsletter and marketing tips, straight to your inbox</p>
  </div>
  <div class="abs" style="left:807px;top:4331px;width:156px;height:39px;background:#f2f2f2;font-size:10px;color:#888;padding:13px 15px">Enter your email</div>
  <a class="btn btn-green" style="left:963px;top:4331px;width:114px;height:39px;font-size:10px">Subscribe</a>
  <div class="abs" style="left:171px;top:4492px;width:863px;height:1px;background:#ddd"></div>
  <p class="abs" style="left:0;width:1200px;text-align:center;top:4512px;font-size:9.5px;color:#444">© 2025 Coral Basins. All rights reserved.</p>
  <svg class="abs" style="left:1142px;top:4474px" width="40" height="36" viewBox="0 0 40 36"><path d="M20 2C10 2 2 8 2 16c0 5 3 9 7 11l-2 8 9-6c1 0 3 .5 4 .5 10 0 18-6 18-13.5S30 2 20 2z" fill="#b7c94f"/><circle cx="13" cy="16" r="2.2" fill="#fff"/><circle cx="20" cy="16" r="2.2" fill="#fff"/><circle cx="27" cy="16" r="2.2" fill="#fff"/></svg>
</footer>

</body>
</html>
```